Webdesign für HALDEN STAHLWERK
Zielgruppe
Valkorin ist Ihr leistungsstarker und zuverlässiger Partner im Bereich Metallverarbeitung. Seit unserer Firmengründung im Jahr 2001 ist unser inhabergeführtes Unternehmen in Gornau bei Chemnitz kontinuierlich gewachsen und beschäftigt derzeit 20 engagierte und qualifizierte Mitarbeiter.
Mit der Einweihung unserer neuen Fertigungshalle 2010 haben wir unsere Produktionsfläche auf 1.400 m2 vergrößert und können Ihnen nun einen noch umfassenderen Service anbieten.
Von der CNC-gesteuerten Teilefertigung bis zu modernsten Schweiß-, Schneid-, und Bearbeitungsanlagen – für die Realisierung Ihrer individuellen Wünsche steht uns ein innovativer Maschinenpark zur Verfügung. Wir fertigen zuverlässig und termingerecht nach Ihren Plänen oder übernehmen bei Bedarf auch die gesamte Abwicklung Ihres Projektes – alles made in germany!
Das Unternehmen spricht ausschließlich B2B Kunden an.
Die Hauptleistungsbereiche sind:
- Stahl- und Palettenbau
- Blechbearbeitung
- Edelstahlbearbeitung
- Mechanische Fertigung
Aufgabenstellung
- Mitlaufende Kontaktleiste
- Integration der Social Media Kanäle
- Sehr modernes Auftreten
- Industrielles Design
- Verlinkung zum Partnerunternehmen https://www.valkorin-beispiel.de/ias/index.html

```html
<!DOCTYPE html>
<html lang="de">
<head>
<meta charset="utf-8">
<title>Valkorin – Metallverarbeitung</title>
<link href="https://fonts.googleapis.com/css2?family=Overpass:wght@400;500;600;700&family=Inter:wght@400;500;600&display=swap" rel="stylesheet">
<style>
:root{
  --blue:#0b3f80;
  --navy:#141b47;
  --ink:#0d1426;
  --accent:#3c8fe3;
  --text:#1b1f2b;
  --muted:#8c93a3;
  --line:#dfe4ee;
  --white:#fff;
}
*{box-sizing:border-box;margin:0;padding:0}
html,body{width:1200px;height:4418px;overflow:hidden}
body{font-family:"Inter",sans-serif;color:var(--text);background:var(--white);position:relative}
h1,h2,h3,.head{font-family:"Overpass",sans-serif}
.abs{position:absolute}
.eyebrow{font-size:9px;letter-spacing:1.6px;text-transform:uppercase;color:var(--accent);font-weight:500}
.title{font-family:"Overpass",sans-serif;font-size:25px;font-weight:600}
.btn{position:absolute;display:flex;align-items:center;justify-content:center;gap:8px;font-size:11px;font-weight:500;border:1.5px solid}
.arrow{width:14px;height:8px}

/* top bar */
.topbar{left:0;top:0;width:1200px;height:30px;background:#f2f3f5;font-size:8px;letter-spacing:.8px;color:#333}
.dot{width:10px;height:10px;border-radius:50%;background:#aab0bc;position:absolute;top:10px}

/* nav */
.nav{left:0;top:30px;width:1200px;height:75px;background:#fff}
.logo{font-family:"Overpass",sans-serif;font-weight:700;font-size:31px;letter-spacing:-1px;color:var(--ink)}
.menu{position:absolute;top:27px;font-size:12px;font-weight:500;display:flex;gap:30px;left:530px}

/* hero */
.hero{left:0;top:105px;width:1200px;height:495px;background:radial-gradient(circle at 55% 40%,#7a6450 0%,#3e3732 40%,#1e1d1f 100%)}
.hero h1{position:absolute;left:0;width:1200px;top:152px;text-align:center;color:#fff;font-weight:500;font-size:37px;line-height:40px}

/* services */
.services{left:0;top:600px;width:1200px;height:1157px;background:var(--blue)}
.card{position:absolute;top:250px;width:211px;height:281px}
.card .ph{position:absolute;left:0;top:0;width:211px;height:253px;clip-path:polygon(0 0,88% 0,100% 10%,100% 100%,0 100%)}
.card .cap{position:absolute;left:0;bottom:0;width:156px;height:56px;background:var(--navy);color:#fff;font-family:"Overpass",sans-serif;font-size:12px;letter-spacing:1.6px;line-height:15px;padding:13px 15px;text-transform:uppercase}

.navybox{left:405px;top:1723px;width:795px;height:248px;background:var(--navy);color:#fff}

.stat{position:absolute;top:2185px;text-align:center;width:230px}
.stat b{display:block;font-family:"Overpass",sans-serif;font-weight:500;font-size:58px;color:var(--accent);line-height:60px}
.stat span{font-size:9px;letter-spacing:1.6px;font-weight:600;text-transform:uppercase}

.news{position:absolute;top:2491px;width:287px}
.news .ph{height:209px}
.tag{display:inline-block;margin-top:18px;background:var(--accent);color:#fff;font-size:8px;border-radius:12px;padding:6px 9px}
.news h3{font-family:"Inter",sans-serif;font-size:11px;font-weight:600;margin-top:12px;letter-spacing:.3px}
.news p{font-size:8px;color:var(--muted);margin-top:7px}

.footer{left:0;top:3814px;width:1200px;height:604px;background:var(--ink);color:#fff}
.fcol{position:absolute;top:233px;font-size:10px;line-height:29px}
.fcol .eyebrow{display:block;line-height:14px;margin-bottom:10px}
</style>
</head>
<body>

<!-- top bar -->
<div class="abs topbar">
  <span class="abs" style="left:40px;top:11px">T: +49 3700 / 120 450 6</span>
  <span class="abs" style="left:175px;top:11px">E: INFO@VALKORIN-BEISPIEL.DE</span>
  <span class="dot" style="left:990px"></span><span class="dot" style="left:1020px"></span><span class="dot" style="left:1050px"></span>
  <span class="dot" style="left:1080px"></span><span class="dot" style="left:1110px"></span><span class="dot" style="left:1140px"></span>
</div>

<!-- nav -->
<header class="abs nav">
  <div class="abs logo" style="left:40px;top:20px">VALKORIN</div>
  <nav class="menu"><span>Home</span><span>Leistungen</span><span>Produkte</span><span>Fertigung</span><span>Qualifikation</span><span>Über Uns</span></nav>
  <div class="abs" style="left:1027px;top:20px;width:1px;height:33px;background:var(--line)"></div>
  <a class="btn" style="left:1063px;top:16px;width:97px;height:39px;color:var(--accent);border-color:var(--accent);font-size:10px">Kontakt
    <svg class="arrow" viewBox="0 0 14 8"><path d="M0 4h13M9 0l4 4-4 4" stroke="currentColor" fill="none"/></svg></a>
</header>

<!-- hero -->
<section class="abs hero" role="img" aria-label="Foto: CNC-Fräse bei der Metallbearbeitung mit Funkenflug">
  <div class="abs" style="left:40px;top:462px;width:1070px;height:1px;background:rgba(255,255,255,.25)"></div>
  <div class="abs" style="left:40px;top:0;width:1px;height:462px;background:rgba(255,255,255,.15)"></div>
  <h1>Ihr zuverlässiger Partner im<br>Bereich der Metallverarbeitung</h1>
  <a class="btn" style="left:437px;top:260px;width:147px;height:39px;background:#fff;border-color:#fff;color:var(--blue)">Angebot einholen
    <svg class="arrow" viewBox="0 0 14 8"><path d="M0 4h13M9 0l4 4-4 4" stroke="currentColor" fill="none"/></svg></a>
  <a class="btn" style="left:604px;top:260px;width:158px;height:39px;border-color:#fff;color:#fff">Jetzt mehr erfahren
    <svg class="arrow" viewBox="0 0 14 8"><path d="M0 4h13M9 0l4 4-4 4" stroke="currentColor" fill="none"/></svg></a>
  <div class="abs" style="left:1109px;top:40px;width:1px;height:60px;background:rgba(255,255,255,.4)"></div>
  <div class="abs" style="left:1102px;top:370px;transform-origin:0 0;transform:rotate(-90deg);white-space:nowrap;font-size:9px;letter-spacing:1.6px;color:#fff">YOUR PARTNER OF EXCELLENCE IN METALWORK</div>
  <svg class="abs" style="left:1080px;top:355px" width="120" height="140"><polygon points="120,0 120,140 0,140" fill="var(--blue)"/></svg>
</section>

<!-- sticky contact strip -->
<div class="abs" style="left:1150px;top:269px;width:50px;height:163px">
  <div class="abs" style="left:0;top:0;width:50px;height:50px;background:var(--accent)"><svg width="50" height="50"><path d="M16 25l18-8-6 18-4-6z" fill="none" stroke="#fff" stroke-width="1.4"/></svg></div>
  <div class="abs" style="left:0;top:56px;width:50px;height:50px;background:var(--accent)"><svg width="50" height="50"><path d="M18 17c0 9 6 15 15 15l1-4-4-2-2 2c-3-1-5-3-6-6l2-2-2-4z" fill="none" stroke="#fff" stroke-width="1.4"/></svg></div>
  <div class="abs" style="left:0;top:112px;width:50px;height:50px;background:var(--accent)"><svg width="50" height="50"><path d="M16 33h18M18 33v-9h14v9M22 24v-6h6v6M22 28v5M28 28v5" fill="none" stroke="#fff" stroke-width="1.4"/></svg></div>
</div>

<!-- services -->
<section class="abs services">
  <div class="abs eyebrow" style="left:151px;top:160px">Leistungen</div>
  <h2 class="abs title" style="left:151px;top:181px;color:#fff">Unsere Leistungsbereiche</h2>
  <div class="abs" style="left:508px;top:194px;width:536px;height:1px;background:rgba(120,170,230,.5)"></div>
  <div class="card" style="left:151px"><div class="ph" role="img" aria-label="Foto: Laserschneidanlage" style="background:linear-gradient(160deg,#4b4a4c,#8a6a4c 55%,#2b2b2e)"></div><div class="cap">Stahl- und<br>Palettenbau</div></div>
  <div class="card" style="left:381px"><div class="ph" role="img" aria-label="Foto: Blechbearbeitung mit Laserfunken" style="background:linear-gradient(160deg,#3b2230,#c0506a 55%,#2a1b26)"></div><div class="cap">Blech-<br>bearbeitung</div></div>
  <div class="card" style="left:610px"><div class="ph" role="img" aria-label="Foto: Techniker mit Tablet zwischen Edelstahlrohren" style="background:linear-gradient(160deg,#d8dde2,#a2a9b2 55%,#5d6b84)"></div><div class="cap">Edelstahl-<br>bearbeitung</div></div>
  <div class="card" style="left:840px"><div class="ph" role="img" aria-label="Foto: Mitarbeiter an einer Fräsmaschine" style="background:linear-gradient(160deg,#c6ccd2,#5a6478 55%,#2c3550)"></div><div class="cap">Mechanische<br>Fertigung</div></div>
  <a class="btn" style="left:490px;top:574px;width:182px;height:38px;border-color:#fff;color:#fff">Alle Leistungen ansehen
    <svg class="arrow" viewBox="0 0 14 8"><path d="M0 4h13M9 0l4 4-4 4" stroke="currentColor" fill="none"/></svg></a>
</section>

<!-- about -->
<div class="abs" role="img" aria-label="Foto: Mitarbeiter bedient eine Fräsmaschine in der Werkhalle" style="left:151px;top:1363px;width:1049px;height:360px;background:linear-gradient(110deg,#dfe4ea 0%,#9aa5b4 35%,#556072 60%,#bfc6cf 100%)"></div>
<svg class="abs" style="left:151px;top:1723px" width="254" height="125"><polygon points="0,0 254,0 254,125 100,125 0,40" fill="#e6e8ec"/></svg>
<section class="abs navybox">
  <div class="abs eyebrow" style="left:60px;top:42px">Ihr zuverlässiger Partner</div>
  <h2 class="abs" style="left:60px;top:60px;font-size:23px;font-weight:500;line-height:32px">Wir vereinen Qualität und<br>Kundenzufriedenheit</h2>
  <div class="abs" style="left:385px;top:42px;width:340px;font-size:10px;line-height:16.5px;color:#c9cde0">
    <p>Lorem ipsum dolor sit amet consectetur. Risus risus dui commodo posuere aenean ac mauris sed. Morbi aliquam tincidunt nibh leo. Quam ipsum sapien mauris pharetra id convallis ac nunc venenatis. Blandit viverra nunc enim sagittis accumsan habitant. Leo elit tellus sapien arcu congue sit malesuada id.</p>
    <p style="margin-top:16px">Vestibulum augue tempus sed scelerisque at tellus. Diam magna commodo donec odio. Quisque eget ridiculus risus placerat fringilla congue sit dolor. Penatibus massa urna egestas velit in tortor nec molestie tincidunt.</p>
  </div>
</section>

<!-- stats -->
<div class="abs eyebrow" style="left:151px;top:2084px">Fakten und Zahlen</div>
<h2 class="abs title" style="left:151px;top:2103px">VALKORIN in Zahlen</h2>
<div class="stat" style="left:134px"><b>22</b><span>Jahre Expertise</span></div>
<div class="stat" style="left:350px"><b>1.400</b><span>m² Produktionsfläche</span></div>
<div class="stat" style="left:579px"><b>20</b><span>Engagierte Mitarbeiter</span></div>
<div class="stat" style="left:829px"><b>100%</b><span>Made in Germany</span></div>
<div class="abs" style="left:350px;top:2197px;width:1px;height:80px;background:var(--line)"></div>
<div class="abs" style="left:580px;top:2197px;width:1px;height:80px;background:var(--line)"></div>
<div class="abs" style="left:809px;top:2197px;width:1px;height:80px;background:var(--line)"></div>

<!-- news -->
<div class="abs eyebrow" style="left:151px;top:2403px">Neuigkeiten rund um die Metallverarbeitung</div>
<h2 class="abs title" style="left:151px;top:2421px">Aktuelles &amp; Neuigkeiten</h2>
<div class="abs" style="left:470px;top:2434px;width:460px;height:1px;background:var(--line)"></div>
<div class="abs" style="left:960px;top:2414px;width:39px;height:39px;border:1px solid var(--line)"><svg width="39" height="39"><path d="M26 19.5H13M17 15.5l-4 4 4 4" stroke="#b9c6dc" fill="none"/></svg></div>
<div class="abs" style="left:1009px;top:2414px;width:39px;height:39px;background:#b9d0ee"><svg width="39" height="39"><path d="M13 19.5h13M22 15.5l4 4-4 4" stroke="var(--blue)" fill="none"/></svg></div>
<article class="news" style="left:151px"><div class="ph" role="img" aria-label="Foto: Laserschneiden von Blech" style="background:linear-gradient(160deg,#3a3a3e,#9a6c48 55%,#232327)"></div><span class="tag">Categorytag</span><h3>LOREM IPSUM DOLOR SIT AMET</h3><p>vom 24. September 2023</p></article>
<article class="news" style="left:457px"><div class="ph" role="img" aria-label="Foto: Metalllamellen einer Fassade" style="background:linear-gradient(100deg,#4e5054,#d6d8dc 50%,#7d8086)"></div><span class="tag">Categorytag</span><h3>LOREM IPSUM DOLOR SIT AMET</h3><p>vom 24. September 2023</p></article>
<article class="news" style="left:763px"><div class="ph" role="img" aria-label="Foto: Metallfassade eines Gebäudes" style="background:linear-gradient(100deg,#8e98a8,#d9dee6 50%,#6f7b8e)"></div><span class="tag">Categorytag</span><h3>LOREM IPSUM DOLOR SIT AMET</h3><p>vom 24. September 2023</p></article>
<a class="btn" style="left:513px;top:2827px;width:152px;height:38px;border-color:var(--blue);color:var(--blue)">Alle News ansehen
  <svg class="arrow" viewBox="0 0 14 8"><path d="M0 4h13M9 0l4 4-4 4" stroke="currentColor" fill="none"/></svg></a>

<!-- partner -->
<div class="abs" style="left:151px;top:3000px;width:893px;height:1px;background:var(--line)"></div>
<div class="abs eyebrow" style="left:151px;top:3065px">Partnerunternehmen</div>
<h2 class="abs title" style="left:151px;top:3083px">Rethmar Anlagenservice</h2>
<p class="abs" style="left:151px;top:3133px;width:510px;font-size:10px;line-height:16.5px;color:var(--blue)">Lorem ipsum dolor sit amet consectetur. Risus risus dui commodo posuere aenean ac mauris sed. Morbi aliquam tincidunt nibh leo. Quam ipsum sapien mauris pharetra id convallis ac nunc venenatis. Blandit viverra nunc enim sagittis accumsan habitant. Leo elit tellus sapien arcu congue sit malesuada id.</p>
<div class="abs" style="left:792px;top:3112px;display:flex;align-items:center;gap:12px">
  <span style="width:40px;height:40px;background:var(--blue);display:block"></span>
  <span class="head" style="font-size:18px;font-weight:600;color:var(--blue);line-height:20px">RETHMAR<br>ANLAGENSERVICE</span>
</div>

<!-- contact -->
<div class="abs" style="left:151px;top:3314px;width:1049px;height:372px;background:var(--blue)"></div>
<div class="abs" style="left:591px;top:3686px;width:609px;height:128px;background:var(--navy)"></div>
<div class="abs footer"></div>
<svg class="abs" style="left:0;top:3411px" width="591" height="506" role="img" aria-label="Foto: lächelnder Techniker mit Helm an einer Maschinensteuerung">
  <defs><linearGradient id="pg" x1="0" y1="0" x2="1" y2="1"><stop offset="0" stop-color="#e3e6ea"/><stop offset=".5" stop-color="#8e98a8"/><stop offset="1" stop-color="#2d3650"/></linearGradient></defs>
  <polygon points="0,0 500,0 591,80 591,506 0,506" fill="url(#pg)"/>
</svg>
<h2 class="abs head" style="left:667px;top:3414px;color:#fff;font-size:24px;font-weight:600">Kontakt</h2>
<div class="abs" style="left:667px;top:3450px;color:#c9d4e8;font-size:10px">So erreichen Sie uns</div>
<svg class="abs" style="left:667px;top:3522px" width="20" height="20"><path d="M3 3c0 8 6 14 14 14l1-4-4-2-2 2c-3-1-5-3-6-6l2-2-2-4z" fill="none" stroke="#fff" stroke-width="1.2"/></svg>
<div class="abs head" style="left:700px;top:3513px;color:#fff;font-size:16px;font-weight:600">+49 3700 / 120 450 00</div>
<div class="abs" style="left:700px;top:3537px;color:var(--accent);font-size:8px;letter-spacing:1px">MO–FR · 08:00 – 18:00</div>
<div class="abs" style="left:667px;top:3563px;width:382px;height:1px;background:rgba(255,255,255,.3)"></div>
<svg class="abs" style="left:667px;top:3590px" width="20" height="20"><path d="M2 10l16-7-6 16-3-6z" fill="none" stroke="#fff" stroke-width="1.2"/></svg>
<div class="abs head" style="left:700px;top:3580px;color:#fff;font-size:16px;font-weight:600">info@valkorin-beispiel.de</div>
<div class="abs" style="left:700px;top:3605px;color:var(--accent);font-size:8px">Wir antworten meist binnen 24 Stunden</div>
<div class="abs" style="left:667px;top:3738px;color:#fff;font-size:11px;line-height:14px">Oder nutzen Sie<br>unser <b>Kontaktformular</b></div>
<a class="btn" style="left:883px;top:3730px;width:166px;height:38px;border-color:#fff;color:#fff">Zum Kontaktformular
  <svg class="arrow" viewBox="0 0 14 8"><path d="M0 4h13M9 0l4 4-4 4" stroke="currentColor" fill="none"/></svg></a>

<!-- footer -->
<footer>
  <div class="abs logo" style="left:151px;top:4038px;color:#fff">VALKORIN</div>
  <div class="abs" style="left:151px;top:4104px;width:260px;font-size:10px;line-height:15px;color:#c5cad6">
    <b style="color:#fff">Valkorin GmbH</b><br>Musterstraße 1<br>12345 Musterstadt<br>Deutschland
    <p style="margin-top:18px">Lorem ipsum dolor sit amet consectetur. Dolor cras eget a volutpat ullamcorper facilisis. Viverra aliquam ac aliquet aliquet odio in aliquet.</p>
  </div>
  <div class="fcol" style="left:454px;top:4047px;color:#fff"><span class="eyebrow">Seiten</span>Leistungen<br>Produkte<br>Fertigung<br>Qualifikation<br>Über uns</div>
  <div class="fcol" style="left:609px;top:4047px;color:#fff"><span class="eyebrow">Rechtliches</span>Impressum<br>Datenschutzerklärung
    <span class="eyebrow" style="margin-top:20px">Kontakt &amp; Sonstiges</span>FAQ<br>Kontakt<br>Links</div>
  <div class="fcol" style="left:838px;top:4047px;color:#fff;line-height:15px"><span class="eyebrow">Kontaktinformationen</span>
    <div style="margin-top:16px">Telefon:<br><span style="color:var(--accent);font-weight:600">+49 3700 / 120 450 00</span></div>
    <div style="margin-top:14px">E-Mail:<br><span style="color:var(--accent);font-weight:600;text-decoration:underline">info@valkorin-beispiel.de</span></div>
  </div>
  <a class="btn" style="left:838px;top:4174px;width:82px;height:34px;border-radius:17px;border-color:#fff;color:#fff">Kontakt</a>
  <div class="abs" style="left:151px;top:4291px;width:893px;height:1px;background:rgba(255,255,255,.15)"></div>
  <div class="abs" style="left:151px;top:4318px;color:#fff;font-size:10px">Copyright © 2023 valkorin-beispiel.de</div>
  <span class="abs" style="left:843px;top:4316px;width:16px;height:16px;border-radius:50%;background:var(--accent)"></span>
  <span class="abs" style="left:881px;top:4316px;width:16px;height:16px;border-radius:50%;background:var(--accent)"></span>
  <span class="abs" style="left:919px;top:4316px;width:16px;height:16px;border-radius:50%;background:var(--accent)"></span>
  <span class="abs" style="left:957px;top:4316px;width:16px;height:16px;border-radius:50%;background:var(--accent)"></span>
  <span class="abs" style="left:995px;top:4316px;width:16px;height:16px;border-radius:50%;background:var(--accent)"></span>
  <span class="abs" style="left:1033px;top:4316px;width:16px;height:16px;border-radius:50%;background:var(--accent)"></span>
</footer>

</body>
</html>
```